Business Card for Coastal Tundrabridge Advisory

We need a business card for Coastal Tundrabridge Advisory. The company website address is provided below. The company logo is attached. We provide specialized permafrost services to the mining, transportation, and oil & gas industries. The card should be prepared for:
Matthias Korhonen, PhD.
Coastal Tundrabridge Advisory
PO Box 418259
Quillwater, Alaska 99642
Direct: +1-907-555-0143
Email: mkorhonen@tundrabridgeadvisory.example
Website: www.coastaltundrabridgeadvisory.example

```html
<!DOCTYPE html>
<html lang="en">
<head>
<meta charset="utf-8">
<title>Coastal Tundrabridge Advisory – Business Card</title>
<link href="https://fonts.googleapis.com/css2?family=Arimo:wght@400;700&display=swap" rel="stylesheet">
<style>
  :root {
    --page: #e4e5e7;
    --ink: #151d27;
    --paper: #ffffff;
    --light: #ffffff;
    --muted: #c9ced6;
    --rule: #6d7580;
  }
  html, body {
    margin: 0;
    width: 1200px;
    height: 800px;
    overflow: hidden;
    background: var(--page);
    font-family: "Arimo", Arial, sans-serif;
  }
  .stage {
    position: relative;
    width: 1200px;
    height: 800px;
  }
  .card {
    position: absolute;
    top: 250px;
    width: 525px;
    height: 300px;
    border-radius: 18px;
    box-sizing: border-box;
    box-shadow: 0 6px 18px rgba(0,0,0,0.12);
  }
  /* Back side: contact details */
  .card-back {
    left: 50px;
    background: var(--ink);
    color: var(--light);
  }
  .card-back .wordmark {
    position: absolute;
    top: 34px;
    right: 34px;
    font-size: 15px;
    font-weight: 700;
    letter-spacing: 2px;
    text-transform: uppercase;
    color: var(--light);
  }
  .card-back .person {
    position: absolute;
    left: 34px;
    top: 150px;
  }
  .person-name {
    font-size: 21px;
    font-weight: 700;
    margin: 0;
  }
  .person-title {
    font-size: 13px;
    margin: 4px 0 0;
    color: var(--muted);
  }
  .card-back .rule {
    position: absolute;
    left: 34px;
    right: 34px;
    top: 204px;
    height: 1px;
    background: var(--rule);
  }
  .contact-list {
    position: absolute;
    left: 34px;
    top: 214px;
    margin: 0;
    padding: 0;
    list-style: none;
    font-size: 12.5px;
    line-height: 20px;
  }
  .contact-list li {
    display: flex;
    align-items: center;
    gap: 8px;
  }
  .contact-list svg {
    width: 11px;
    height: 11px;
    fill: var(--light);
    flex: none;
  }
  .address {
    position: absolute;
    right: 34px;
    top: 150px;
    text-align: right;
    font-size: 13px;
    line-height: 20px;
    font-style: normal;
  }
  /* Front side: name mark */
  .card-front {
    left: 625px;
    background: var(--paper);
    display: flex;
    align-items: center;
    justify-content: center;
    gap: 12px;
  }
  .card-front .wordmark {
    font-size: 24px;
    font-weight: 700;
    letter-spacing: 2px;
    text-transform: uppercase;
    color: var(--ink);
    text-align: center;
    line-height: 1.3;
  }
</style>
</head>
<body>
<main class="stage">
  <section class="card card-back">
    <div class="wordmark">Coastal Tundrabridge Advisory</div>
    <div class="person">
      <p class="person-name">Matthias Korhonen, PhD.</p>
      <p class="person-title">President</p>
    </div>
    <address class="address">PO Box 418259<br>Quillwater, Alaska 99642</address>
    <div class="rule"></div>
    <ul class="contact-list">
      <li>
        <svg viewBox="0 0 12 12" aria-hidden="true"><path d="M2.5 0.5l2 2.2-1 1.4c.7 1.6 2 2.9 3.5 3.6l1.4-1 2.1 2-1 1.8C5 10.5 1.2 6.7.7 1.5z"/></svg>
        <span>+1-907-555-0143</span>
      </li>
      <li>
        <svg viewBox="0 0 12 12" aria-hidden="true"><path d="M0 2h12v8H0z M1 3l5 3.5L11 3" stroke="#151d27" stroke-width="0.9"/></svg>
        <span>mkorhonen@tundrabridgeadvisory.example</span>
      </li>
      <li>
        <svg viewBox="0 0 12 12" aria-hidden="true"><circle cx="6" cy="6" r="5.5"/><path d="M0.5 6h11M6 .5c-2.5 3-2.5 8 0 11M6 .5c2.5 3 2.5 8 0 11" stroke="#151d27" stroke-width="0.8" fill="none"/></svg>
        <span>www.coastaltundrabridgeadvisory.example</span>
      </li>
    </ul>
  </section>

  <section class="card card-front">
    <div class="wordmark">Coastal Tundrabridge<br>Advisory</div>
  </section>
</main>
</body>
</html>
```